The Moodbreakers---near future sci-fi thriller book cover

This is a near-future science-fiction thriller in which a software engineer and a nurse become unlikely allies as they attempt to stop a bizarre epidemic of aggression and paranoia.

It's 2034, and society is dominated by technology and almost bankrupt of direct human contact. Lorna Vasquell is a nurse in the "neuro ward" at Pellham Hospital in Atlanta when her youngest brother becomes one of the first victims of what is soon dubbed Acute Hostility Syndrome. When Lorna suspects a technological cause, her strange, beautiful, antisocial new acquaintance, Tessa Quillon, a software engineer, agrees to help. Tessa may be part of the cure... or she may be the cause... or maybe she'll prove to be indifferent to the fates of thousands of people, including Lorna's brother.

The cover definitely needs to say SCIENCE FICTION. Ideally it should say THRILLER as well. And maybe HACKING.

There are two female main characters so any people portrayed should be women. One has curly blonde hair and one has straight brown hair; both are Caucasian.

The main plot centers around hacking and around the devices that are called Orlix that are basically smartphones implanted in people's brains.

The Moodbreakers
J.L.M. Dorvan

The design needs to be suitable for PRINT (trade paperback) as well as ebook (so please show front and back covers in the design).

Reason: Waiting for a tweak from one of the designers... and allowing time for my friends to vote on the poll.

Target Market(s)

People who like near-future sci-fi thrillers.

Industry/Entity Type

Software

Font styles to use
Serif
Sans Serif

Requirements
Nice to have
• Ideas...
• 1) a female eye (or set of eyes) that is modified to look cybernetic in some way, on a high-tech looking background
• 2) two women's faces side-by-side, both Caucasian, one with long straight brown hair and one with long curly blonde hair, with the brunette having "weird" eyes---a color that isn't natural for brunettes or cybernetic looking or something. The blonde would have normal blue eyes.
• 3) a woman with a malevolent look and one or both eyes cybernetic looking
• 4) The first half or two third of the book is in hospitals. So, people in white coats melded into an interesting tech-looking background might be good.
• 6) In general, people looking like they could be crazy people (straitjackets? or just facial expressions or something) melded with high-tech-looking elements.
• A good background might be a night-time big city. Not recognizable as any particular city, though.
• http://thumbs.pixelvaultex.com/z/chicago-skyline-night-20206447.jpg
• http://i.framequarry.com/file_thumbview_approve/24891344/2/stock-photo-24891344-new-york-night-skyline.jpg
• http://www.pixelvaultex.com/royalty-free-stock-photo-new-york-city-night-image14052405
Should not have
• Cyborgs or robots.
• UFOs.
• A recognizable skyline unless it is Atlanta, Georgia.
• Male people (the two main characters are female, so let's make any people on the front cover female)... unless you're doing the "crazy people" cover, in which case, the primary character who goes crazy in the book is a 18-year-old white male with blond curly hair.
• "THE" should not be larger than "MOODBREAKERS." It is okay to hyphenate MOODBREAKERS into two lines:
• MOOD-
• BREAKERS

```html
<!DOCTYPE html>
<html lang="en">
<head>
<meta charset="utf-8">
<title>The Moodbreakers — Cover Spread</title>
<link href="https://fonts.googleapis.com/css2?family=Bebas+Neue&family=Crimson+Text&family=Oswald:wght@600&display=swap" rel="stylesheet">
<style>
  :root {
    --ink-black: #0b0709;
    --title-cream: #f4efdc;
    --night-deep: #0a1118;
    --night-teal: #2f7f86;
    --sky-glow: #bfeee8;
    --city-amber: #d98a2e;
    --city-dark: #1b1210;
    --isbn-white: #f7f5ef;
  }
  html, body {
    margin: 0;
    padding: 0;
    width: 1200px;
    height: 854px;
    overflow: hidden;
    background: #ffffff;
  }
  .spread {
    position: relative;
    width: 1200px;
    height: 854px;
    overflow: hidden;
    background: var(--ink-black);
  }
  .back-cover,
  .front-cover {
    position: absolute;
    top: 0;
    height: 854px;
    overflow: hidden;
  }
  .back-cover { left: 0; width: 563px; }
  .front-cover { left: 630px; width: 570px; }

  .back-art {
    position: absolute;
    inset: 0;
    background:
      radial-gradient(ellipse 60% 30% at 45% 75%, rgba(217,138,46,0.35), transparent 70%),
      radial-gradient(ellipse 50% 40% at 10% 40%, rgba(120,150,170,0.35), transparent 70%),
      linear-gradient(180deg, #0d1620 0%, #15232e 35%, #2a2320 65%, #120c0a 85%, #0a0708 100%);
  }
  .front-art {
    position: absolute;
    inset: 0;
    background:
      radial-gradient(circle at 32% 38%, rgba(235,255,250,0.95) 0, rgba(191,238,232,0.6) 6%, rgba(47,127,134,0.35) 22%, transparent 45%),
      radial-gradient(ellipse 70% 25% at 40% 72%, rgba(217,138,46,0.45), transparent 70%),
      linear-gradient(180deg, #102a33 0%, #1f5c63 25%, #1c3c46 42%, #241c1a 62%, #15100e 82%, #090607 100%);
  }
  .window-frame {
    position: absolute;
    inset: 0;
    pointer-events: none;
  }

  .book-title {
    margin: 0;
    font-family: "Bebas Neue", "Oswald", sans-serif;
    font-weight: 400;
    color: var(--title-cream);
    white-space: nowrap;
    line-height: 1;
    text-shadow: 0 2px 6px rgba(0,0,0,0.6);
  }
  .book-author {
    margin: 0;
    font-family: "Oswald", sans-serif;
    font-weight: 600;
    color: var(--title-cream);
    white-space: nowrap;
    line-height: 1;
  }

  .back-title {
    position: absolute;
    top: 62px;
    left: 0;
    width: 580px;
    text-align: center;
    font-size: 50px;
  }
  .back-author {
    position: absolute;
    top: 128px;
    left: 0;
    width: 580px;
    text-align: center;
    font-size: 22px;
    letter-spacing: 0.62em;
    text-indent: 0.62em;
  }
  .blurb {
    position: absolute;
    top: 178px;
    left: 88px;
    width: 417px;
    font-family: "Crimson Text", serif;
    font-size: 13.6px;
    line-height: 17.5px;
    color: var(--title-cream);
    text-align: justify;
    text-align-last: center;
  }
  .blurb p { margin: 0 0 17.5px; }
  .isbn-box {
    position: absolute;
    left: 355px;
    top: 706px;
    width: 186px;
    height: 110px;
    background: var(--isbn-white);
  }

  .spine {
    position: absolute;
    left: 563px;
    top: 0;
    width: 67px;
    height: 854px;
    background: var(--ink-black);
  }
  .spine-title {
    position: absolute;
    left: 6px;
    top: 50px;
    writing-mode: vertical-rl;
    font-size: 52px;
  }
  .spine-author {
    position: absolute;
    left: 20px;
    top: 540px;
    writing-mode: vertical-rl;
    font-size: 22px;
    letter-spacing: 0.6em;
  }

  .front-title {
    position: absolute;
    top: 92px;
    left: 0;
    width: 570px;
    text-align: center;
    font-size: 68px;
  }
  .front-author {
    position: absolute;
    top: 776px;
    left: 0;
    width: 570px;
    text-align: center;
    font-size: 30px;
    letter-spacing: 0.62em;
    text-indent: 0.62em;
  }
  .heroine {
    position: absolute;
    left: 330px;
    top: 170px;
    width: 215px;
    height: 640px;
    background: linear-gradient(180deg, rgba(160,90,60,0.55) 0%, rgba(20,22,26,0.85) 25%, rgba(10,12,14,0.9) 100%);
    border-radius: 90px 90px 20px 20px;
  }
</style>
</head>
<body>
<main class="spread">

  <section class="back-cover">
    <div class="back-art" role="img" aria-label="Night-time city lights seen through a tall window frame under a dark starry sky"></div>
    <svg class="window-frame" width="563" height="854" aria-hidden="true">
      <rect x="0" y="98" width="563" height="18" fill="rgba(8,6,8,0.6)"/>
      <rect x="0" y="395" width="563" height="16" fill="rgba(8,6,8,0.55)"/>
      <rect x="150" y="0" width="16" height="560" fill="rgba(8,6,8,0.45)"/>
      <rect x="470" y="0" width="16" height="560" fill="rgba(8,6,8,0.45)"/>
    </svg>
    <h2 class="book-title back-title">THE MOODBREAKERS</h2>
    <p class="book-author back-author">J.L.M. DORVAN</p>
    <div class="blurb">
      <p>Lorem ipsum dolor sit amet, consectetuer adipiscing elit. Aenean commodo ligula eget dolor. Aenean massa. Cum sociis natoque penatibus et magnis dis parturient montes, nascetur ridiculus mus. Donec quam felis, ultricies nec, pellentesque eu, pretium quis, sem. Nulla consequat massa quis enim. Donec pede justo, fringilla vel, aliquet nec, vulputate eget, arcu. In enim justo, rhoncus ut, imperdiet a, venenatis vitae, justo. Nullam dictum felis eu pede mollis pretium. Integer tincidunt.</p>
      <p>Cras dapibus. Vivamus elementum semper nisi. Aenean vulputate eleifend tellus. Aenean leo ligula, porttitor eu, consequat vitae, eleifend ac, enim. Aliquam lorem ante, dapibus in, viverra quis, feugiat a, tellus. Phasellus viverra nulla ut metus varius laoreet. Quisque rutrum. Aenean imperdiet. Etiam ultricies nisi vel augue. Curabitur ullamcorper ultricies nisi. Nam eget dui. Etiam rhoncus. Maecenas tempus, tellus eget condimentum rhoncus, sem quam semper libero, sit amet adipiscing sem neque sed ipsum. Nam quam nunc, blandit vel, luctus pulvinar, hendrerit id, lorem. Maecenas nec odio et ante tincidunt tempus.</p>
      <p>Donec vitae sapien ut libero venenatis faucibus. Nullam quis ante. Etiam sit amet orci eget eros faucibus tincidunt. Duis leo. Sed fringilla mauris sit amet nibh. Donec sodales sagittis magna. Sed consequat, leo eget bibendum sodales, augue velit cursus nunc.</p>
    </div>
    <div class="isbn-box"></div>
  </section>

  <section class="spine">
    <h2 class="book-title spine-title">THE MOODBREAKERS</h2>
    <p class="book-author spine-author">J.L.M. DORVAN</p>
  </section>

  <section class="front-cover">
    <div class="front-art" role="img" aria-label="Glowing teal night sky with falling binary code over a city of lights, seen through a large window frame"></div>
    <svg class="window-frame" width="570" height="854" aria-hidden="true">
      <rect x="0" y="255" width="570" height="14" fill="rgba(8,6,8,0.55)"/>
      <rect x="0" y="562" width="570" height="12" fill="rgba(8,6,8,0.5)"/>
      <rect x="170" y="0" width="18" height="700" fill="rgba(8,6,8,0.55)"/>
      <rect x="372" y="150" width="16" height="550" fill="rgba(8,6,8,0.5)"/>
    </svg>
    <div class="heroine" role="img" aria-label="A red-haired woman in a black leather coat and tall boots standing in front of the window"></div>
    <h1 class="book-title front-title">THE MOODBREAKERS</h1>
    <p class="book-author front-author">J.L.M. DORVAN</p>
  </section>

</main>
</body>
</html>
```